VTMB site redesign

Please redesign a home page with content provided. PSD only - no coding
Can use any images from Snapwelder.com

Please create a site design that more clearly illustrates the client's services and expertise. We are looking for a high-end design.

Any images used must be generic or of Dallas TX.

Fonts: Any
Colors: Match to logo
Look: Modern - Professional

Target Market(s)

medium-large business owners

Number of Pages Required

1 page

Font styles to use
Serif
Sans Serif

Requirements
Must have
• cohesive professional design
• high end look
• Match to logo

```html
<!DOCTYPE html>
<html lang="en">
<head>
<meta charset="utf-8">
<title>VTMB – Vantmore Commercial Real Estate Group</title>
<link rel="stylesheet" href="https://fonts.googleapis.com/css2?family=Crimson+Text:ital,wght@0,400;0,600;0,700;1,400&family=Open+Sans:wght@400;600;700&display=swap">
<style>
:root{
  --red:#b3121c;
  --red-dark:#8f0d15;
  --ink:#1b1b1b;
  --text:#555;
  --muted:#8a8a8a;
  --light:#f2f2f2;
  --white:#fff;
  --footer:#232527;
  --serif:"Crimson Text", Georgia, serif;
  --sans:"Open Sans", Arial, sans-serif;
}
*{margin:0;padding:0;box-sizing:border-box}
html,body{width:1200px;height:4215px;overflow:hidden}
body{position:relative;font-family:var(--sans);color:var(--text);background:var(--white)}
.abs{position:absolute}
.btn{position:absolute;background:var(--red);color:#fff;font:600 15px var(--sans);text-transform:uppercase;border-radius:30px;display:flex;align-items:center;justify-content:center;box-shadow:0 4px 8px rgba(0,0,0,.25)}
.section-title{position:absolute;left:0;width:1200px;text-align:center;font:700 38px var(--serif);color:var(--red)}
.social{display:flex;gap:10px}
.social i{display:block;width:10px;height:10px;border-radius:50%;background:currentColor;opacity:.7}

/* top bar + nav */
.topbar{left:0;top:0;width:1200px;height:48px;background:var(--ink);color:#fff}
.topbar .phone{position:absolute;left:830px;top:14px;font:600 16px var(--sans);display:flex;gap:10px;align-items:center}
.topbar .social{position:absolute;left:1040px;top:19px;color:#fff}
.navbar{left:0;top:48px;width:1200px;height:78px;background:#fff}
.nav{position:absolute;left:440px;top:28px;display:flex;gap:0;font:15px var(--sans);color:#555}
.nav span{padding:0 20px}
.nav .active{color:var(--red);border-bottom:3px solid var(--red);padding-bottom:20px}
.nav-search{left:1076px;top:62px;width:46px;height:46px;border-radius:50%;border:2px solid var(--red)}
.brand{left:79px;top:0;width:230px;height:126px;background:var(--red);display:flex;align-items:center;justify-content:center;font:700 62px var(--serif);color:#fff;letter-spacing:2px;box-shadow:0 4px 10px rgba(0,0,0,.3)}

/* hero */
.hero{left:0;top:126px;width:1200px;height:571px;background:linear-gradient(180deg,#3a4452 0%,#5b6572 45%,#35383e 100%)}
.hero-kicker{top:270px;width:1200px;text-align:center;font:700 15px var(--serif);color:#fff;letter-spacing:1px;text-transform:uppercase}
.hero-title{top:290px;width:1200px;text-align:center;font:700 84px var(--serif);color:#fff;line-height:1}
.hero-sub{top:383px;width:1200px;text-align:center;font:36px var(--serif);color:#fff}
.search{left:253px;top:463px;width:697px;height:62px;border-radius:31px;background:#fff;display:flex;overflow:hidden;box-shadow:0 0 0 4px rgba(255,255,255,.25)}
.search .field{width:235px;padding:0 24px;display:flex;align-items:center;font:15px var(--sans);color:#999;border-right:1px solid #ddd}
.search .go{flex:1;background:var(--red);color:#fff;font:600 20px var(--sans);display:flex;align-items:center;justify-content:center;margin-left:0}

/* about */
.about-title{left:79px;top:756px;font:700 40px var(--serif);color:var(--red)}
.about-text{left:79px;top:830px;width:540px;font:14px/26px var(--sans);color:var(--text)}
.about-photo{left:680px;top:778px;width:440px;height:296px;background:linear-gradient(135deg,#e8eaeb,#b9bec2 60%,#8d9296);box-shadow:0 3px 10px rgba(0,0,0,.25);border:5px solid #fff}

/* services */
.services{left:0;top:1138px;width:1200px;height:674px;background:var(--light)}
.card{position:absolute;background:#fff;box-shadow:0 3px 12px rgba(0,0,0,.15);text-align:center}
.card .photo{position:absolute;left:0;top:0;width:100%;height:210px}
.card h3{position:absolute;top:230px;width:100%;font:700 26px var(--serif);color:var(--red)}
.card p{position:absolute;left:28px;right:28px;top:280px;font:13px/24px var(--sans);color:var(--text)}

/* team */
.team-intro{left:300px;top:1933px;width:600px;text-align:center;font:13px/24px var(--sans);color:var(--text)}
.member{position:absolute;top:2107px;width:287px;height:428px;background:#fff;box-shadow:0 3px 12px rgba(0,0,0,.15);text-align:center}
.member .photo{position:absolute;left:8px;top:8px;right:8px;height:280px}
.member .role{position:absolute;top:308px;width:100%;font:13px var(--sans);color:#333}
.member .name{position:absolute;top:330px;width:100%;font:600 26px var(--serif);color:var(--red)}
.member .social{position:absolute;top:380px;left:0;width:100%;justify-content:center;color:#888}

/* band */
.band{left:0;top:2607px;width:1200px;height:332px;background:linear-gradient(90deg,#1c1c1c,#3a3a3a 55%,#2a2a2a)}
.band-text{left:240px;top:2660px;width:720px;text-align:center;font:italic 34px/42px var(--serif);color:#fff}

/* testimonial */
.quote-mark{left:0;top:3060px;width:1200px;text-align:center;font:700 110px/1 var(--serif);color:var(--ink)}
.quote-text{left:225px;top:3145px;width:750px;text-align:center;font:13px/24px var(--sans);color:var(--text)}
.thumb{position:absolute;top:3280px;width:96px;height:96px;border:3px solid #fff;box-shadow:0 2px 6px rgba(0,0,0,.2)}
.thumb-active{position:absolute;left:491px;top:3262px;width:117px;height:122px;background:#c9515a;color:#fff;font:15px/20px var(--serif);text-transform:uppercase;display:flex;align-items:center;justify-content:center;text-align:center}
.arrow{position:absolute;top:3312px;width:36px;height:36px;border-radius:50%;display:flex;align-items:center;justify-content:center}

/* cta */
.cta{left:0;top:3473px;width:1200px;height:264px;background:#111}
.cta-text{left:79px;top:3530px;width:720px;font:27px/38px var(--serif);color:#fff}
.cta-red{left:0;top:3473px}
.cta-call{left:842px;top:3532px;font:27px/38px var(--serif);color:#fff}
.cta-phone{left:842px;top:3620px;font:700 26px var(--sans);color:#fff;display:flex;align-items:center;gap:16px}

/* footer */
.footer{left:0;top:3737px;width:1200px;height:416px;background:linear-gradient(180deg,#2b2d30,#1d1f21)}
.f-title{position:absolute;top:3795px;font:22px var(--serif);color:#fff}
.f-item{position:absolute;font:13px/22px var(--sans);color:#ddd;display:flex;gap:14px}
.f-nav{left:382px;top:3848px;font:14px/40px var(--sans);color:#ddd}
.f-nav div::before{content:"»";margin-right:14px;color:#aaa}
.post{position:absolute;left:548px;display:flex;gap:16px}
.post .pic{width:92px;height:92px;background:linear-gradient(135deg,#d7dadc,#8c949b)}
.post .txt{width:170px;font:13px/21px var(--sans);color:#eee}
.post .date{margin-top:8px;color:#bbb}
.news-text{left:868px;top:3840px;width:260px;font:13px/21px var(--sans);color:#ddd}
.news-form{left:868px;top:3947px;width:252px;height:44px;border-radius:22px;background:#fff;overflow:hidden}
.news-form span{position:absolute;left:18px;top:12px;font:14px var(--sans);color:#777}
.news-form .send{position:absolute;right:0;top:0;width:84px;height:44px;background:#20639b;border-radius:22px;display:flex;align-items:center;justify-content:center}
.f-circles{left:912px;top:4020px;display:flex;gap:12px}
.f-circles i{display:block;width:34px;height:34px;border-radius:50%;background:#1f5f96;border:2px solid #fff}
.copyright{left:0;top:4153px;width:1200px;height:62px;background:var(--red);color:#fff;font:13px var(--sans);display:flex;align-items:center;justify-content:center}
</style>
</head>
<body>

<header>
  <div class="abs topbar">
    <div class="phone">
      <svg width="16" height="16" viewBox="0 0 24 24"><path fill="#fff" d="M6.6 10.8a15 15 0 0 0 6.6 6.6l2.2-2.2c.3-.3.7-.4 1-.2 1.1.4 2.3.6 3.6.6.6 0 1 .4 1 1V20c0 .6-.4 1-1 1A17 17 0 0 1 3 4c0-.6.4-1 1-1h3.5c.6 0 1 .4 1 1 0 1.3.2 2.5.6 3.6.1.3 0 .7-.2 1z"/></svg>
      555-014-2626
    </div>
    <div class="social"><i></i><i></i><i></i></div>
  </div>
  <div class="abs navbar">
    <nav class="nav">
      <span>Home</span><span class="active">About VTMB</span><span>Services</span><span>Market News</span><span>Blog</span><span>Contact Us</span>
    </nav>
  </div>
  <svg class="abs nav-search" viewBox="0 0 46 46"><circle cx="21" cy="21" r="7" fill="none" stroke="#b3121c" stroke-width="2.5"/><line x1="26" y1="26" x2="31" y2="31" stroke="#b3121c" stroke-width="2.5"/></svg>
  <div class="abs brand">VTMB</div>
</header>

<section>
  <div class="abs hero" role="img" aria-label="Street of modern Dallas office buildings with parked cars at dusk"></div>
  <div class="abs hero-kicker">Dallas Commercial Realty since 1982</div>
  <h1 class="abs hero-title">VTMB</h1>
  <div class="abs hero-sub">Vantmore Commercial Real Estate Group</div>
  <div class="abs search">
    <div class="field">Location</div>
    <div class="field" style="justify-content:space-between">Keyword <svg width="12" height="8" viewBox="0 0 12 8"><path d="M1 1l5 5 5-5" fill="none" stroke="#333" stroke-width="2"/></svg></div>
    <div class="go">SEARCH</div>
  </div>
</section>

<section>
  <h2 class="abs about-title">About VTMB</h2>
  <p class="abs about-text">At VTMB, we focus solely on office and industrial/warehouse commercial real estate leasing and sales in the greater Dallas/Fort Worth area. We believe that our unique commercial office space service and market knowledge is the key to our clients' growth and ultimate business success. We strive to learn the specific needs of your company and be an essential team member that will find the best solution for your commercial real estate needs.</p>
  <div class="btn" style="left:79px;top:1017px;width:160px;height:54px">Read More</div>
  <div class="abs about-photo" role="img" aria-label="Bright modern office lobby with reception desk"></div>
</section>

<section>
  <div class="abs services"></div>
  <h2 class="section-title" style="top:1195px">VTMB Services</h2>
  <div class="card" style="left:84px;top:1287px;width:332px;height:458px">
    <div class="photo" role="img" aria-label="Suburban house with red tile roof and lawn" style="background:linear-gradient(180deg,#8fb6d8,#b7755a 55%,#5f8a3c)"></div>
    <h3>Services 1</h3>
    <p>Lorem Ipsum is simply dummy text of the printing and typesetting industry. Lorem dummy text ever since the 1500s.</p>
    <div class="btn" style="left:90px;top:382px;width:152px;height:48px">Read More</div>
  </div>
  <div class="card" style="left:441px;top:1287px;width:318px;height:458px">
    <div class="photo" role="img" aria-label="Modern glass office building among trees" style="background:linear-gradient(180deg,#a9c6e0,#7c8a96 55%,#4f6b3e)"></div>
    <h3>Services 2</h3>
    <p>Lorem Ipsum is simply dummy text of the printing and typesetting industry. Lorem dummy text ever since the 1500s.</p>
    <div class="btn" style="left:83px;top:382px;width:152px;height:48px">Read More</div>
  </div>
  <div class="card" style="left:798px;top:1287px;width:320px;height:458px">
    <div class="photo" role="img" aria-label="Contemporary office block with grey facade" style="background:linear-gradient(180deg,#6f9fd0,#9aa4ad 60%,#6d7378)"></div>
    <h3>Services 3</h3>
    <p>Lorem Ipsum is simply dummy text of the printing and typesetting industry. Lorem dummy text ever since the 1500s.</p>
    <div class="btn" style="left:84px;top:382px;width:152px;height:48px">Read More</div>
  </div>
</section>

<section>
  <h2 class="section-title" style="top:1872px">Meet the Team</h2>
  <p class="abs team-intro">At VTMB we believe that you deserve the best professional advice and personal service with your commercial real estate negotiations. By choosing VTMB as your tenant reps in the Dallas/Fort Worth area, you will receive the assistance of accomplished and experienced commercial real estate brokers and salespeople who are licensed by the State Realty Licensing Board to practice in Texas since 1982.</p>
  <div class="member" style="left:112px">
    <div class="photo" role="img" aria-label="Portrait of a commercial property specialist" style="background:linear-gradient(135deg,#e6e1da,#9fb2c6)"></div>
    <div class="role">Commercial Property Specialist</div>
    <div class="name">Owen Carter-Hale</div>
    <div class="social"><i></i><i></i><i></i><i></i></div>
  </div>
  <div class="member" style="left:455px">
    <div class="photo" role="img" aria-label="Portrait of the founder and president" style="background:linear-gradient(135deg,#e9e9ea,#3b4a66)"></div>
    <div class="role">Founder and President</div>
    <div class="name">Reid T. Vantmore</div>
    <div class="social"><i></i><i></i><i></i><i></i></div>
  </div>
  <div class="member" style="left:804px">
    <div class="photo" role="img" aria-label="Portrait of a junior associate tenant rep specialist" style="background:linear-gradient(135deg,#cfc7bd,#4b4b4f)"></div>
    <div class="role">Jr., Associate, Tenant Rep Specialist</div>
    <div class="name">Daniel James Rowe</div>
    <div class="social"><i></i><i></i><i></i><i></i></div>
  </div>
</section>

<section>
  <div class="abs band" role="img" aria-label="Business people reviewing documents at a desk"></div>
  <p class="abs band-text">If you need to find office or warehouse space in the Dallas Fort Worth area, the team at VTMB has the experience you need.</p>
  <div class="btn" style="left:490px;top:2818px;width:220px;height:52px">Space Calculator</div>
</section>

<section>
  <h2 class="section-title" style="top:2998px">Client Testimonial</h2>
  <div class="abs quote-mark">&ldquo;</div>
  <p class="abs quote-text">The real estate team at VTMB has decades of experience in Commercial. One advantage of VTMB is they know all the properties that are about to become available, BEFORE they are available. They have the inside track on properties and they watch your back at the negotiating table. Very impressive with a polished approach. Let the team run with your next project and you won't be disappointed.</p>
  <div class="arrow" style="left:320px;background:var(--red)"><svg width="12" height="14" viewBox="0 0 12 14"><path d="M9 1L3 7l6 6" fill="none" stroke="#fff" stroke-width="2.5"/></svg></div>
  <div class="thumb" role="img" aria-label="Client photo" style="left:387px;background:linear-gradient(135deg,#eee,#b8b2aa)"></div>
  <div class="thumb-active">Paul<br>Benning</div>
  <div class="thumb" role="img" aria-label="Client photo" style="left:614px;background:linear-gradient(135deg,#eef2f5,#a9b9c6)"></div>
  <div class="thumb" role="img" aria-label="Client photo" style="left:717px;background:linear-gradient(135deg,#f3f3f3,#c4b7ad)"></div>
  <div class="arrow" style="left:845px;background:var(--ink)"><svg width="12" height="14" viewBox="0 0 12 14"><path d="M3 1l6 6-6 6" fill="none" stroke="#fff" stroke-width="2.5"/></svg></div>
</section>

<section>
  <div class="abs cta"></div>
  <svg class="abs cta-red" width="1200" height="264" viewBox="0 0 1200 264"><polygon points="818,0 1200,0 1200,264 780,264" fill="#fff"/><polygon points="826,0 1200,0 1200,264 788,264" fill="#b3121c"/></svg>
  <p class="abs cta-text">Looking for commercial real estate in the DFW area? Fill out the form below and use our FREE location service to find it for you!</p>
  <div class="btn" style="left:79px;top:3640px;width:184px;height:50px">Contact Form</div>
  <p class="abs cta-call">We are ready to receive<br>your call</p>
  <div class="abs cta-phone">
    <svg width="28" height="28" viewBox="0 0 24 24"><path fill="#fff" d="M6.6 10.8a15 15 0 0 0 6.6 6.6l2.2-2.2c.3-.3.7-.4 1-.2 1.1.4 2.3.6 3.6.6.6 0 1 .4 1 1V20c0 .6-.4 1-1 1A17 17 0 0 1 3 4c0-.6.4-1 1-1h3.5c.6 0 1 .4 1 1 0 1.3.2 2.5.6 3.6.1.3 0 .7-.2 1z"/></svg>
    555-014-2626
  </div>
</section>

<footer>
  <div class="abs footer" role="img" aria-label="Dark city skyline at night"></div>
  <div class="f-title" style="left:79px">Our Company</div>
  <div class="f-item" style="left:79px;top:3850px">
    <svg width="14" height="20" viewBox="0 0 14 20"><path d="M7 0a7 7 0 0 0-7 7c0 5 7 13 7 13s7-8 7-13a7 7 0 0 0-7-7zm0 10a3 3 0 1 1 0-6 3 3 0 0 1 0 6z" fill="#fff"/></svg>
    <div><b style="color:#fff;font-size:15px">Office Address</b><br><span style="display:block;margin-top:8px">4120 Elmwood Avenue @<br>Crestline Suite 720 Dallas,<br>Texas 75201</span></div>
  </div>
  <div class="f-item" style="left:79px;top:3985px"><svg width="14" height="14" viewBox="0 0 24 24"><path fill="#fff" d="M6.6 10.8a15 15 0 0 0 6.6 6.6l2.2-2.2c.3-.3.7-.4 1-.2 1.1.4 2.3.6 3.6.6.6 0 1 .4 1 1V20c0 .6-.4 1-1 1A17 17 0 0 1 3 4c0-.6.4-1 1-1h3.5c.6 0 1 .4 1 1 0 1.3.2 2.5.6 3.6.1.3 0 .7-.2 1z"/></svg>555-014-2626</div>
  <div class="f-item" style="left:79px;top:4025px"><svg width="14" height="14" viewBox="0 0 14 14"><rect x="1" y="4" width="12" height="8" fill="#fff"/><rect x="3" y="1" width="8" height="4" fill="none" stroke="#fff"/></svg>555-018-3299</div>
  <div class="f-item" style="left:79px;top:4065px"><svg width="14" height="12" viewBox="0 0 14 12"><rect x="0.5" y="0.5" width="13" height="11" fill="none" stroke="#fff"/><path d="M1 1l6 5 6-5" fill="none" stroke="#fff"/></svg>info@vtmbrealty.com</div>

  <div class="f-title" style="left:382px">Navigation</div>
  <div class="abs f-nav"><div>Home</div><div>About</div><div>Services</div><div>Market News</div><div>Blog</div><div>Contact</div></div>

  <div class="f-title" style="left:548px">Recent Articals</div>
  <div class="post" style="top:3848px"><div class="pic" role="img" aria-label="Article thumbnail"></div><div class="txt">Lorem Ipsum simply dummy printing text<div class="date">May, 07 2018</div></div></div>
  <div class="post" style="top:3970px"><div class="pic" role="img" aria-label="Article thumbnail"></div><div class="txt">Lorem Ipsum simply dummy printing text<div class="date">May, 07 2018</div></div></div>

  <div class="f-title" style="left:868px">Newsletter</div>
  <p class="abs news-text">Lorem Ipsum is simply dummy text of the printing and typesetting industry. Lorem Ipsum has been the industry's.</p>
  <div class="abs news-form"><span>Email</span><div class="send"><svg width="22" height="20" viewBox="0 0 22 20"><path d="M1 9L21 1l-5 18-5-7z" fill="#fff"/></svg></div></div>
  <div class="abs f-circles"><i></i><i></i><i></i><i></i></div>

  <div class="abs copyright">Copyright © VANTMORE COMMERCIAL REALTY GROUP - 2018 All Rights Reserved.</div>
</footer>

</body>
</html>
```